Custom unique Stationary design for Logistics company

We need a custom, unique , elegant and luxurious full stationary design using our new logo, following these guidelines:
1- Business card: double sided, both sides uses the navy blue as the background main color (same as the code of the navy blue used in our logo).
2- envelope and folder: also use the same navy blue as the main background color.
3- book cover( notepad cover) : same thing with the navy blue
4- letterhead: feel free to use the combination of the colors in our logo.
5- rest of the items are up to your creativity

Target Market(s)

corporates and other businesses

Industry/Entity Type

Logistics and heavy machines contractors

Requirements
Must have
• Letterhead, business card, envelope, notepad cover, paper, file
Nice to have
• navy blue to be main background color for business card, envelope, notepad cover

```html
<!DOCTYPE html>
<html lang="en">
<head>
<meta charset="utf-8">
<title>Norvale Freight Group – Business Card</title>
<link href="https://fonts.googleapis.com/css2?family=Karla:wght@400;500;700&family=Archivo:wght@700&display=swap" rel="stylesheet">
<style>
  :root {
    --navy: #134a70;
    --orange: #ea5520;
    --paper: #f6f6f4;
    --backdrop: #2a2b2e;
    --ink: #1f2326;
  }
  * { box-sizing: border-box; margin: 0; padding: 0; }
  html, body { width: 1200px; height: 874px; overflow: hidden; }
  body {
    background: var(--backdrop);
    font-family: "Karla", sans-serif;
    position: relative;
  }
  .card {
    position: absolute;
    left: 280px;
    width: 640px;
    height: 366px;
    border-radius: 22px;
    overflow: hidden;
  }
  .card--back { top: 50px; background: var(--navy); }
  .card--front { top: 458px; background: var(--paper); }

  .card__wave { position: absolute; inset: 0; width: 100%; height: 100%; }

  .wordmark {
    font-family: "Karla", sans-serif;
    font-weight: 700;
    color: #ffffff;
    line-height: 1;
    display: flex;
    align-items: center;
    gap: 14px;
  }
  .wordmark__dot {
    width: 16px; height: 16px;
    border-radius: 50%;
    background: #ffffff;
    flex: none;
  }
  .wordmark__text span { display: block; }
  .card--back .wordmark {
    position: absolute;
    inset: 0;
    justify-content: center;
    font-size: 52px;
    letter-spacing: 1px;
  }
  .card--back .wordmark__tag { font-size: 22px; letter-spacing: 4px; margin-top: 6px; }
  .card--front .wordmark {
    position: absolute;
    left: 40px; top: 66px;
    font-size: 34px;
    letter-spacing: 0.5px;
  }
  .card--front .wordmark__tag { font-size: 15px; letter-spacing: 3px; margin-top: 4px; }

  .holder {
    position: absolute;
    right: 42px; top: 58px;
    text-align: right;
  }
  .holder__name {
    font-family: "Archivo", sans-serif;
    font-weight: 700;
    font-size: 24px;
    color: var(--orange);
    text-transform: uppercase;
    letter-spacing: 0.3px;
  }
  .holder__title {
    font-size: 16px;
    color: #ffffff;
    margin-top: 4px;
    letter-spacing: 0.5px;
  }

  .contacts {
    position: absolute;
    right: 34px; bottom: 18px;
    list-style: none;
    color: var(--ink);
    font-size: 13.5px;
    text-align: right;
    letter-spacing: 0.3px;
  }
  .contacts li {
    display: flex;
    justify-content: flex-end;
    align-items: center;
    gap: 10px;
    line-height: 1.3;
  }
  .contacts__address { margin-bottom: 6px; }
  .contacts__icon { width: 13px; height: 13px; flex: none; fill: var(--orange); }
</style>
</head>
<body>

  <section class="card card--back" aria-label="Business card, back">
    <div class="wordmark">
      <i class="wordmark__dot"></i>
      <div class="wordmark__text"><span>NORVALE</span><span class="wordmark__tag">FREIGHT GROUP</span></div>
    </div>
  </section>

  <section class="card card--front" aria-label="Business card, front">
    <svg class="card__wave" viewBox="0 0 640 366" aria-hidden="true">
      <path class="wave__accent-left" d="M0 150 C60 270 170 355 270 325 C170 372 50 292 0 172 Z" fill="var(--orange)"/>
      <path class="wave__field" d="M0 0 H640 V250 C590 200 530 180 470 190 C390 205 350 300 270 325 C170 355 60 270 0 150 Z" fill="var(--navy)"/>
      <path class="wave__accent-right" d="M640 242 C590 192 530 172 470 182 C400 195 370 258 330 290 C372 246 400 172 468 160 C540 150 598 180 640 220 Z" fill="var(--orange)"/>
    </svg>

    <div class="wordmark">
      <i class="wordmark__dot"></i>
      <div class="wordmark__text"><span>NORVALE</span><span class="wordmark__tag">FREIGHT GROUP</span></div>
    </div>

    <div class="holder">
      <p class="holder__name">Daniel Hart</p>
      <p class="holder__title">President</p>
    </div>

    <ul class="contacts">
      <li class="contacts__address">
        <span>412 Harbor View Road<br>Juneau, Alaska 99801</span>
        <svg class="contacts__icon" viewBox="0 0 14 14"><path d="M7 0a5 5 0 0 0-5 5c0 3.5 5 9 5 9s5-5.5 5-9a5 5 0 0 0-5-5zm0 7a2 2 0 1 1 0-4 2 2 0 0 1 0 4z"/></svg>
      </li>
      <li>
        <span>555-201-7730</span>
        <svg class="contacts__icon" viewBox="0 0 14 14"><path d="M3 1l2.5 3-1.5 1.5c.8 1.8 2.2 3.2 4 4L9.5 8 13 10.5 11.5 13C6 13 1 8 1 2.5z"/></svg>
      </li>
      <li>
        <span>555-208-4416</span>
        <svg class="contacts__icon" viewBox="0 0 14 14"><path d="M4 0h6a1 1 0 0 1 1 1v12a1 1 0 0 1-1 1H4a1 1 0 0 1-1-1V1a1 1 0 0 1 1-1zm.5 1.5v10h5v-10z"/></svg>
      </li>
      <li>
        <span>daniel@norvale.com</span>
        <svg class="contacts__icon" viewBox="0 0 14 14"><path d="M0 3h14v8H0zm1.2 1L7 8l5.8-4z"/></svg>
      </li>
      <li>
        <span>www.norvale.com</span>
        <svg class="contacts__icon" viewBox="0 0 14 14"><circle cx="7" cy="7" r="6.5"/><path d="M7 .5v13M.5 7h13" stroke="#f6f6f4" stroke-width="1" fill="none"/></svg>
      </li>
    </ul>
  </section>

</body>
</html>
```